Business Identity Stationary

Already have the logo which is in the attached files so only need the Business STationary
1) Double Sided Business Card
2) Letterhead
3) Presentation folder with business card holder on inside cover
4) WIth compliments slip
See information for business cards, letterhead and presentation folder below.

This should be a simply job using a logo we already had designed along with a little device. I suggest using the device off center and perhaps lower in the corner in an abstract way. Also the logo device could be used as a watermark for the letterhead. The designer who created the logo presented something that I think works well for a business card. The front of the double sided business card could have the name logo small for the website address and only use the Lime device on the front. Then on the back could be the name Barrow Advisory logo.

Please note that for the business card the black and lime green background do look good. Also please think of using the lime device separately in an unusual way.

It has been brought to my attention that.my budget was far to low. Hopefully this.will attract you to the project. 

The parent company of Barrow Advisory is TallHeron holdings. I have uploaded a file of the Tall Heron business card I really like. Perhaps use this business card as a guide to the type of modern and clean style I am looking for. It also works to have the Barrow Advisroy and Tall Heron similar.

Reason: Still haven't received anything exactly right.

Industry/Entity Type

Business

Font styles to use
Sans Serif

Colors
9bcb3c
000000
5c5c5c
add136
cadf82
eaf2cf
f9fbf2
1b1b1b
757575

Requirements
Must have
• 1) Double Sided Business Card
Marta Kellendorf
Director
Tel: +505 8264 3170
Email: mk@barrowadvisory-example.com
Website: www.barrowadvisory-example.com

Frederick Kellendorf
Director
Tel: +505 8264 3172
Email: fk@barrowadvisory-example.com

Lucia Brenes Otaduy
Director
Tel: 8642 1093
Email: lbo@barrowadvisory-example.com

2) Letterhead
Logo
Lime Logo Device
Website Address: www.barrowadvisory-example.com
Small print on bottom: Barrow Advisory a Tall Heron Holding Company SA. RUC J0487000239518

3) Presentation Folder
Traditional Presentation folder with inside front cover spot for the insertion of business card.

4) With Compliments slip

```html
<!DOCTYPE html>
<html lang="en">
<head>
<meta charset="utf-8">
<title>Barrow Advisory – Presentation Folder</title>
<link rel="stylesheet" href="https://fonts.googleapis.com/css2?family=Questrial&display=swap">
<style>
  :root {
    --lime: #add136;
    --lime-deep: #9bcb3c;
    --black: #000000;
    --ink: #1b1b1b;
    --graphite: #5c5c5c;
    --white: #ffffff;
    --backdrop: #2a2a2a;
  }
  html, body {
    margin: 0;
    padding: 0;
    width: 1200px;
    height: 840px;
    overflow: hidden;
    background: var(--backdrop);
  }
  .canvas {
    position: relative;
    width: 1200px;
    height: 840px;
    font-family: "Questrial", "Century Gothic", sans-serif;
  }
  .folder {
    position: absolute;
    left: 330px;
    top: 60px;
    width: 540px;
    height: 720px;
    background: var(--black);
    overflow: hidden;
    box-shadow: 0 10px 30px rgba(0,0,0,0.5);
  }
  .folder__brand {
    position: absolute;
    left: 48px;
    top: 64px;
    display: flex;
    align-items: center;
    gap: 14px;
    white-space: nowrap;
  }
  .brand__name {
    color: var(--white);
    font-size: 36px;
    letter-spacing: 2px;
    text-transform: uppercase;
    line-height: 1;
    margin: 0;
    font-weight: 400;
    white-space: nowrap;
  }
  .brand__dot {
    flex: none;
    width: 20px;
    height: 20px;
    border-radius: 50%;
    background: var(--lime);
  }
  .folder__pocket-edge {
    position: absolute;
    left: 0;
    right: 0;
    bottom: 92px;
    height: 4px;
    background: var(--graphite);
  }
  .folder__band {
    position: absolute;
    left: 0;
    right: 0;
    bottom: 0;
    height: 92px;
    background: var(--lime);
    overflow: hidden;
  }
  .band__url {
    position: absolute;
    left: 24px;
    right: 86px;
    top: 50%;
    transform: translateY(-50%);
    margin: 0;
    white-space: nowrap;
    text-align: center;
    color: var(--ink);
    font-size: 18px;
    letter-spacing: 1.5px;
    text-transform: uppercase;
  }
  .band__rules {
    position: absolute;
    right: 14px;
    top: 0;
    height: 92px;
    width: 60px;
  }
</style>
</head>
<body>
  <main class="canvas">
    <section class="folder" aria-label="Presentation folder front cover">
      <header class="folder__brand">
        <h1 class="brand__name">Barrow Advisory</h1>
        <span class="brand__dot" aria-hidden="true"></span>
      </header>
      <div class="folder__pocket-edge" aria-hidden="true"></div>
      <footer class="folder__band">
        <p class="band__url">www.barrowadvisory-example.com</p>
        <svg class="band__rules" viewBox="0 0 60 92" aria-hidden="true">
          <rect x="4" y="0" width="3" height="92" fill="var(--ink)"/>
          <rect x="20" y="0" width="3" height="92" fill="var(--ink)"/>
          <rect x="40" y="0" width="3" height="92" fill="var(--ink)"/>
        </svg>
      </footer>
    </section>
  </main>
</body>
</html>
```